Facebook post - Kestrel Bay Finishes has arrived to make your tiles smile!

Kestrel Bay Finishes would like to release a Facebook post calling out to the market that we have arrived. The company has a new and fresh branding aiming for a female demographic between the ages of 40 and 55 located in the South West of Western Australia. The company image MUST be centered around trust! Our Primary aim is to create an uncompromising trust from the very first impression. Our logo tag line is, 'We love to make your tiles smile'.
I need 5 x facebook template designs and also 5 x posts.
Our 1st campaign is to be 5 x posts centered around the arrival of this fantastic new company.
We are company that provides the services of:
- Grout and silicone repair.
- Broken or drummy tile replacement and;
- Grout sealing
Dont forget that we must communicate TRUST and the we love to make your tiles SMILE!

```html
<!DOCTYPE html>
<html lang="en">
<head>
<meta charset="utf-8">
<title>Make Your Tiles Smile</title>
<link rel="stylesheet" href="https://fonts.googleapis.com/css2?family=Oswald:wght@300;400&display=swap">
<style>
  :root {
    --tile-white: #fefefe;
    --grout: #d3d5d7;
    --grout-shadow: rgba(120, 124, 128, 0.35);
    --brand-blue: #2fa6dc;
    --brand-blue-soft: #d6edf8;
    --ink-grey: #58585a;
  }
  html, body {
    margin: 0;
    padding: 0;
    width: 1200px;
    height: 1200px;
    overflow: hidden;
    background: var(--grout);
  }
  .post {
    position: relative;
    width: 1200px;
    height: 1200px;
    overflow: hidden;
    background: var(--grout);
    font-family: "Oswald", "Arial Narrow", sans-serif;
  }
  .tile-wall {
    position: absolute;
    left: -483px;
    top: -471px;
    display: grid;
    grid-template-columns: repeat(4, 532px);
    grid-template-rows: repeat(4, 532px);
    gap: 12px;
  }
  .tile {
    background: var(--tile-white);
    border-radius: 4px;
    box-shadow:
      inset 0 0 0 1px rgba(255,255,255,0.9),
      inset 0 0 10px 3px rgba(170, 174, 178, 0.45),
      0 0 4px 1px var(--grout-shadow);
  }
  .line {
    position: absolute;
    margin: 0;
    font-weight: 300;
    text-transform: uppercase;
    line-height: 1;
    white-space: nowrap;
  }
  .line--love {
    left: 138px;
    top: 291px;
    font-size: 85px;
    letter-spacing: 0.235em;
    color: var(--brand-blue);
  }
  .line--make {
    right: 114px;
    top: 258px;
    font-size: 85px;
    letter-spacing: 0.227em;
    color: var(--ink-grey);
  }
  .line--tiles {
    right: 119px;
    top: 349px;
    font-size: 62px;
    letter-spacing: 0.227em;
    color: var(--ink-grey);
  }
  .line--smile {
    right: 112px;
    top: 803px;
    font-size: 107px;
    font-weight: 400;
    letter-spacing: 0.228em;
    color: var(--brand-blue);
  }
  .smile-mark {
    position: absolute;
    left: 122px;
    top: 851px;
    width: 392px;
    height: 50px;
    border-radius: 25px;
    background: linear-gradient(180deg, var(--brand-blue-soft), #a9d8ef);
  }
</style>
</head>
<body>
  <main class="post">
    <div class="tile-wall" aria-hidden="true">
      <div class="tile"></div><div class="tile"></div><div class="tile"></div><div class="tile"></div>
      <div class="tile"></div><div class="tile"></div><div class="tile"></div><div class="tile"></div>
      <div class="tile"></div><div class="tile"></div><div class="tile"></div><div class="tile"></div>
      <div class="tile"></div><div class="tile"></div><div class="tile"></div><div class="tile"></div>
    </div>

    <p class="line line--love">We Love</p>
    <p class="line line--make">To Make</p>
    <p class="line line--tiles">Your Tiles</p>

    <div class="smile-mark" role="img" aria-label="Curved blue smile mark"></div>

    <p class="line line--smile">Smile!</p>
  </main>
</body>
</html>
```